Video Production Company Website

A video production company website for "Copper Fern Productions"
Home page must have video player and way to select between 3 different videos.

Company does video Post production : Editing, Motion Graphics, Color correction, and Aerial videography
Attached company Logo

Design should be simple but Pro looking..

Earthy color palette with slight texture..

Industry/Entity Type

Film Production

Number of Pages Required

3 page

Font styles to use
Sans Serif
Other font styles liked:

Requirements
Nice to have
• Thumbnails on homepage to past project clips
Should not have
• full page video

```html
<!DOCTYPE html>
<html lang="en">
<head>
<meta charset="utf-8">
<title>Copper Fern Productions</title>
<link href="https://fonts.googleapis.com/css2?family=Roboto:wght@300;400;500;700;900&display=swap" rel="stylesheet">
<style>
:root{
  --header:#2c3a37;
  --brand:#8cc04a;
  --accent:#e07a2c;
  --ink:#2b2b2b;
  --muted:#8a8a8a;
  --band:#3b3d3c;
  --footer:#333534;
  --footer-deep:#262827;
  --line:#e4e4e4;
  --white:#fff;
}
*{box-sizing:border-box;margin:0;padding:0}
html,body{width:713px;height:1200px;overflow:hidden;background:var(--white)}
body{font-family:'Roboto',Arial,sans-serif;color:var(--ink);position:relative}
.site-header{position:absolute;top:0;left:0;width:713px;height:52px;background:var(--header);display:flex;align-items:center;padding:0 44px 0 59px}
.brand{font-weight:900;font-size:19px;color:var(--brand);letter-spacing:-.3px}
.nav{margin-left:auto;display:flex;align-items:center;gap:6px}
.nav a{color:var(--white);font-size:9px;text-decoration:none;padding:7px 11px}
.nav a.active{background:var(--accent);border-radius:2px}
.search{width:20px;height:20px;border-radius:50%;background:#4a5855;display:flex;align-items:center;justify-content:center;margin-left:8px}
.hero{position:absolute;top:52px;left:0;width:713px;height:316px;background:linear-gradient(90deg,#b8602a 0%,#d48a4e 30%,#c9a27c 52%,#5b4a3c 68%,#2a2522 85%,#5d5148 100%)}
.hero-copy{position:absolute;left:59px;top:114px;width:240px;color:var(--white)}
.hero h1{font-size:22px;font-weight:700;margin-bottom:10px}
.hero p{font-size:8.5px;line-height:1.5;opacity:.9}
.btn-dark{display:inline-block;margin-top:16px;background:#2a2a2a;color:var(--white);font-size:8.5px;padding:10px 16px;border-radius:2px}
.section-title{text-align:center;font-size:19px;font-weight:700;color:var(--ink)}
.section-sub{text-align:center;font-size:9px;color:var(--muted);margin-top:8px}
.projects{position:absolute;top:404px;left:0;width:713px}
.project-grid{display:flex;gap:11px;margin:24px 0 0 59px}
.project{width:191px}
.thumb{position:relative;height:148px;background:linear-gradient(135deg,#2f3f5a,#6f7d96 50%,#253045);overflow:hidden}
.project:nth-child(2) .thumb{background:linear-gradient(135deg,#1d3b7a,#5a6fb0 45%,#c9c2a8 80%)}
.project:nth-child(3) .thumb{background:linear-gradient(135deg,#3d4a6a,#9aa6c0 50%,#e2e0dc)}
.side-tools{position:absolute;right:4px;top:6px;display:flex;flex-direction:column;gap:3px}
.side-tools span{width:14px;height:14px;background:rgba(0,0,0,.55)}
.player{position:absolute;left:0;right:0;bottom:0;height:20px;background:rgba(0,0,0,.7);display:flex;align-items:center;padding:0 6px;gap:6px}
.bar{flex:1;height:3px;background:#666}
.bar i{display:block;width:30%;height:3px;background:var(--accent)}
.project h3{font-size:8.5px;font-weight:700;margin:14px 0 5px}
.project p{font-size:7.5px;line-height:1.5;color:var(--muted)}
.about{position:absolute;top:708px;left:0;width:713px;height:136px;background:var(--band) repeating-linear-gradient(45deg,rgba(255,255,255,.02) 0 2px,transparent 2px 5px);text-align:center;color:#cfcfcf;padding-top:26px}
.about h2{color:var(--white);font-size:19px;margin-bottom:12px}
.about p{font-size:8.5px;line-height:1.6;width:600px;margin:0 auto}
.about .more{display:block;margin-top:8px;font-size:8px;color:var(--white)}
.services{position:absolute;top:852px;left:59px;width:600px}
.services .section-title,.services .section-sub{text-align:left}
.service-grid{display:flex;gap:26px;margin-top:24px}
.service{display:flex;gap:12px;width:183px}
.service svg{flex:none}
.service h4{font-size:9px;font-weight:500;margin:4px 0 8px}
.service p{font-size:7px;line-height:1.5;color:var(--muted)}
.site-footer{position:absolute;top:1010px;left:0;width:713px;height:143px;background:var(--footer);color:#b4b4b4;display:flex;gap:0;padding:18px 0 0 59px}
.fcol{width:160px;padding-right:18px}
.fcol h5{font-size:7.5px;color:var(--white);font-weight:500;letter-spacing:.5px;margin-bottom:14px}
.fcol p,.fcol li{font-size:6.5px;line-height:1.5;list-style:none}
.fcol li{margin-bottom:9px}
.fcol li small{display:block;color:var(--white)}
.contact-row{display:flex;gap:6px;margin-bottom:10px}
.contact-row svg{flex:none}
.field{height:18px;background:#444746;margin:10px 0 8px;width:140px}
.btn-sub{display:inline-block;background:#1f2120;color:var(--white);font-size:6.5px;padding:6px 12px}
.bottom-bar{position:absolute;top:1153px;left:0;width:713px;height:47px;background:var(--footer-deep);display:flex;align-items:center;padding:0 20px 0 59px;color:#9a9a9a;font-size:6.5px}
.bottom-bar nav{color:var(--white);margin-bottom:4px}
.social{margin-left:auto;display:flex;align-items:center;gap:8px}
.social span{width:14px;height:14px;border-radius:50%;background:#444}
.to-top{width:18px;height:18px;background:#444;margin-left:14px}
</style>
</head>
<body>

<header class="site-header">
  <div class="brand">Copper Fern</div>
  <nav class="nav">
    <a class="active">Home</a><a>About</a><a>Services</a><a>Videos</a><a>Contact</a>
    <span class="search"><svg width="9" height="9" viewBox="0 0 10 10"><circle cx="4" cy="4" r="3" fill="none" stroke="#fff" stroke-width="1.3"/><line x1="6.3" y1="6.3" x2="9" y2="9" stroke="#fff" stroke-width="1.3"/></svg></span>
  </nav>
</header>

<section class="hero" role="img" aria-label="Close-up photo of a video camera lens on warm orange background">
  <div class="hero-copy">
    <h1>We do Video Post Production</h1>
    <p>Neque porro quisquam est, qui dolorem ipsum quia dolor sit amet, consectetur, adipisci velit, sed quia non numquam.</p>
    <span class="btn-dark">Click More Info</span>
  </div>
</section>

<section class="projects">
  <h2 class="section-title">Past Projects</h2>
  <p class="section-sub">Simply dummy text of the printing and typesetting industry. Lorem Ipsum has been the industry's standard dummy text</p>
  <div class="project-grid">
    <article class="project">
      <div class="thumb" role="img" aria-label="Video still from a past project">
        <div class="side-tools"><span></span><span></span><span></span></div>
        <div class="player"><svg width="7" height="8"><path d="M0 0L7 4L0 8Z" fill="#fff"/></svg><div class="bar"><i></i></div><svg width="8" height="8"><rect width="8" height="8" fill="none" stroke="#fff"/></svg></div>
      </div>
      <h3>Duis aute irure dolor in reprehenderit</h3>
      <p>Neque porro quisquam est qui dolorem ipsum quia dolor sit amet, adipisci velit, sed quia non numquam eius modi tempora.</p>
    </article>
    <article class="project">
      <div class="thumb" role="img" aria-label="Video still with promotional title card">
        <div class="side-tools"><span></span><span></span><span></span></div>
        <div class="player"><svg width="7" height="8"><path d="M0 0L7 4L0 8Z" fill="#fff"/></svg><div class="bar"><i></i></div><svg width="8" height="8"><rect width="8" height="8" fill="none" stroke="#fff"/></svg></div>
      </div>
      <h3>Duis aute irure dolor in reprehenderit</h3>
      <p>Neque porro quisquam est qui dolorem ipsum quia dolor sit amet, adipisci velit, sed quia non numquam eius modi tempora.</p>
    </article>
    <article class="project">
      <div class="thumb" role="img" aria-label="Video still with bold title text">
        <div class="side-tools"><span></span><span></span><span></span></div>
        <div class="player"><svg width="7" height="8"><path d="M0 0L7 4L0 8Z" fill="#fff"/></svg><div class="bar"><i></i></div><svg width="8" height="8"><rect width="8" height="8" fill="none" stroke="#fff"/></svg></div>
      </div>
      <h3>Duis aute irure dolor in reprehenderit</h3>
      <p>Neque porro quisquam est qui dolorem ipsum quia dolor sit amet, adipisci velit, sed quia non numquam eius modi tempora.</p>
    </article>
  </div>
</section>

<section class="about">
  <h2>About Us</h2>
  <p>We are a small post production studio that shapes raw footage into clear, moving stories. From first cut to final grade we work closely with every client to keep their vision at the heart of the edit.</p>
  <span class="more">Read More »</span>
</section>

<section class="services">
  <h2 class="section-title">Our Services</h2>
  <p class="section-sub">Simply dummy text of the printing and typesetting industry. Lorem Ipsum has been the industry's standard dummy text</p>
  <div class="service-grid">
    <div class="service">
      <svg width="34" height="34" viewBox="0 0 34 34"><rect x="3" y="8" width="28" height="18" fill="#2b2b2b"/><g fill="#fff"><rect x="5" y="10" width="3" height="3"/><rect x="11" y="10" width="3" height="3"/><rect x="17" y="10" width="3" height="3"/><rect x="23" y="10" width="3" height="3"/><rect x="5" y="21" width="3" height="3"/><rect x="11" y="21" width="3" height="3"/><rect x="17" y="21" width="3" height="3"/><rect x="23" y="21" width="3" height="3"/></g></svg>
      <div><h4>Editing</h4><p>Sharp cuts and steady pacing that turn long footage into a tight, clear story for any screen.</p></div>
    </div>
    <div class="service">
      <svg width="34" height="34" viewBox="0 0 34 34"><rect x="3" y="5" width="28" height="19" rx="2" fill="none" stroke="#2b2b2b" stroke-width="2"/><path d="M10 20L15 12L19 17L22 14L26 20Z" fill="#2b2b2b"/><rect x="14" y="24" width="6" height="4" fill="#2b2b2b"/><rect x="10" y="28" width="14" height="2" fill="#2b2b2b"/></svg>
      <div><h4>Motion Graphics</h4><p>Titles, lower thirds and animated graphics that give every project a polished finish.</p></div>
    </div>
    <div class="service">
      <svg width="34" height="34" viewBox="0 0 34 34"><circle cx="17" cy="17" r="12" fill="none" stroke="#2b2b2b" stroke-width="6" stroke-dasharray="6 3"/></svg>
      <div><h4>Color correction</h4><p>Balanced tones and rich grading that give your footage a warm, consistent cinematic look.</p></div>
    </div>
  </div>
</section>

<footer class="site-footer">
  <div class="fcol">
    <h5>CONTACT US</h5>
    <div class="contact-row"><svg width="8" height="10" viewBox="0 0 8 10"><path d="M4 0a4 4 0 0 1 4 4c0 3-4 6-4 6S0 7 0 4a4 4 0 0 1 4-4z" fill="#888"/></svg><p>Copper Fern Productions<br>48 Alder Lane, Brookfield</p></div>
    <div class="contact-row"><svg width="8" height="10" viewBox="0 0 8 10"><rect x="1" y="0" width="6" height="10" rx="1" fill="#888"/></svg><p>(+1) 555 302 8841</p></div>
    <div class="contact-row"><svg width="9" height="7" viewBox="0 0 9 7"><rect width="9" height="7" fill="#888"/><path d="M0 0L4.5 4L9 0" stroke="#333" fill="none"/></svg><p>hello@copperfern.example</p></div>
  </div>
  <div class="fcol">
    <h5>RECENT EVENTS</h5>
    <ul>
      <li>Short film night at the studio with a live edit demo<small>» Find Out</small></li>
      <li>Open house for new clients and local filmmakers<small>» Find Out</small></li>
      <li>Color grading workshop for beginners this spring<small>» Find Out</small></li>
    </ul>
  </div>
  <div class="fcol">
    <h5>RECENT NEWS</h5>
    <ul>
      <li>New aerial footage package now open for booking<small>» Read More</small></li>
      <li>Our latest music video edit wins a regional award<small>» Read More</small></li>
      <li>Studio upgrade brings faster review and delivery<small>» Read More</small></li>
    </ul>
  </div>
  <div class="fcol">
    <h5>NEWSLETTER</h5>
    <p>Sign up for studio news and new project releases.</p>
    <div class="field"></div>
    <span class="btn-sub">SUBSCRIBE</span>
  </div>
</footer>

<div class="bottom-bar">
  <div>
    <nav>Home · Resources · Services · Videos · Contact</nav>
    <div>© Copper Fern Productions 2015. All Rights Reserved.</div>
  </div>
  <div class="social">Connect With Us <span></span><span></span><span></span><span></span><span></span></div>
  <div class="to-top"></div>
</div>

</body>
</html>
```